Residential Mortgage Leader needs Wordpress Design

Looking for a home page website design for a client. We develop using the WordPress platform and would prefer the design be at least loosely based on an existing WordPress template. Attached files have many notes from our creative brief with client. The site must be responsive. Approved, basic wireframe attached. There is room for interpretation.

Existing web site: http://www.marisolkettering.example/

Marisol Kettering relies on strong systems to deliver an on-time, done-right, friendly experience. Marisol offers mortgages and refinancing services throughout the United States. She is a successful Brookvale Funding agent who strives to be an active part of her community. She would like to focus the site on her team, rather than just her.

Difference makers...
When you work with Marisol Kettering you get a high level of expertise and a friendly experience.

She has amazing credentials. Marisol is widely recognized as a top producer for her company, and has earned a number of awards and honors for her customer service.

Marisol's team is very engaged and enjoys sharing social comments or photos from their community.

Imagery:
* Friendly, warm imagery, preferably of her team or an image to represent her team
* Clean and crisp
* Professional / Experts in mortgage and refinance
* Clean / Good use of white space
Updates

When possible, please use imagery from the DFW area. The client mentioned they would prefer not to see stock images. Thanks.

Amend that- creative use of stock images, however, is fine. A few designs have used stock imagery, but in a well-considered manner.

We added some photos and graphics that are local. We are Dallas / Ft. Worth, Plano, Frisco, Texas. We also added some examples of photos to use for the "In the Community" area. Stock photos of business folks just doesn't fit there. Thanks!

Target Market(s)

They service a lot of builders, but also work with homeowners. Their typical client is usually a woman searching for mortgage services online. She typically has a family and may refer her husband to Marisol's team. Keep in mind, however, they also see a number of other scenarios. Most of their clients are middle to high-end borrowers.

Industry/Entity Type

It Company

Requirements
Must have
• Design should be developed using program such as Photoshop or Fireworks or Illustrator as last preference. Ideally, the design would be based on an existing responsive WordPress theme, which we would customize. You must include the name of the target theme. The footer should include lots of space for disclaimers and legal language. Site navigation should include these choices: "Home, About, Builders, Mortgage Info, Approval, Blog, Contact"
Nice to have
• Blog, social media and photos area. Use of the already approved style prototype with colors and fonts (Lato- a Google font, Times New Roman and Cookie-a decorative Google font). However, we are open to interpretation.
Should not have
• Hard to read fonts or a lack of white space.

```html
<!DOCTYPE html>
<html lang="en">
<head>
<meta charset="utf-8">
<title>Brookvale Funding – Marisol Kettering Team</title>
<link href="https://fonts.googleapis.com/css2?family=Rokkitt:wght@400;600&family=Josefin+Slab:wght@400;600&family=Oswald:wght@500&display=swap" rel="stylesheet">
<style>
:root{
  --red:#c4301c;
  --red-dark:#9e2212;
  --ink:#2b2b2b;
  --muted:#777;
  --hero:#252525;
  --nav:#3b3b3b;
  --paper:#efefef;
  --footer:#2a2a2a;
  --footer-base:#1d1d1d;
}
*{box-sizing:border-box;margin:0;padding:0}
html,body{width:900px;height:1200px;overflow:hidden}
body{position:relative;background:var(--paper);font-family:"Josefin Slab",serif;color:var(--ink)}
.abs{position:absolute}
.photo{background:linear-gradient(135deg,#c9d0d6,#7d8791);}
.photo.warm{background:linear-gradient(135deg,#b9a48c,#5f6a72);}

/* header */
.site-header{left:0;top:0;width:900px;height:97px;background:linear-gradient(#fff,#f2f2f2)}
.brand{left:76px;top:30px;font-family:"Rokkitt",serif;font-weight:600;font-size:29px;color:var(--red);display:flex;align-items:center;gap:8px}
.brand-dot{width:14px;height:14px;border-radius:50%;background:var(--red)}
.brand-sub{left:77px;top:62px;font-family:Arial,sans-serif;font-size:12px;color:#555;font-weight:bold}
.contact{right:76px;top:12px;text-align:right;font-family:"Rokkitt",serif}
.contact .label{color:var(--red);font-size:15px}
.contact .phone{font-size:19px;color:#333;letter-spacing:1px;margin-top:1px}
.contact .mail{color:var(--red);font-size:11.5px;margin-top:5px}

/* nav */
.main-nav{left:0;top:97px;width:900px;height:31px;background:linear-gradient(#474747,var(--nav));border-bottom:1px solid #222}
.main-nav a{position:absolute;top:0;height:31px;line-height:31px;font-family:Arial,sans-serif;font-size:11px;color:#fff;text-decoration:none;transform:translateX(-50%)}
.main-nav a.active{background:var(--red);width:50px;text-align:center;transform:none;left:76px}
.main-nav .sep{position:absolute;top:6px;width:1px;height:20px;background:#555}

/* hero */
.hero{left:0;top:128px;width:900px;height:290px;background:var(--hero)}
.hero-frame{left:76px;top:27px;width:352px;height:239px;background:#e8e8e8;padding:6px}
.hero-frame .photo{width:100%;height:100%}
.hero h1{left:442px;top:40px;font-family:"Rokkitt",serif;font-weight:400;font-size:29px;color:var(--red)}
.hero p{left:443px;top:82px;width:363px;font-size:10.4px;line-height:16.5px;color:#d8d8d8;text-align:justify}
.hero p b{color:#f0f0f0}
.btn{left:441px;top:217px;width:164px;height:40px;background:linear-gradient(#d33a22,var(--red-dark));border-radius:4px;color:#fff;font-family:"Rokkitt",serif;font-size:20px;letter-spacing:1px;line-height:40px;padding-left:18px}
.dash{height:0;border-top:2px dashed #cfcfcf}

/* credentials */
.cred h2{font-family:"Rokkitt",serif;font-weight:400}
.cred .lead{color:var(--red);font-size:30px}
.cred .plain{font-size:24px;color:#333}
.cred .tag{font-family:"Rokkitt",serif;font-size:12px;margin-top:2px}
.cred p{font-size:9.6px;line-height:13.6px;color:#888;text-align:justify;width:215px}

.community-title{left:0;width:900px;top:608px;text-align:center;font-family:"Rokkitt",serif;font-size:26px;color:var(--red)}
.community-sub{left:0;width:900px;top:642px;text-align:center;font-family:"Rokkitt",serif;font-size:13px;color:#222;letter-spacing:.5px}
.section-h{font-family:"Rokkitt",serif;font-size:20px;color:#222;letter-spacing:.5px}
.blog-list{left:85px;top:728px;list-style:none}
.blog-list li{height:27px;font-family:"Rokkitt",serif;font-size:12px;letter-spacing:.6px;color:#222;display:flex;align-items:center;gap:9px}
.post{left:271px;width:275px;display:flex;gap:9px}
.post .thumb{width:52px;height:44px;border:2px solid #fff;box-shadow:0 0 1px #999;flex:none}
.post .txt{font-size:9.6px;line-height:13.5px;color:#888;text-align:justify}
.post .txt b{color:#333;font-weight:600;font-size:10px}
.post .more{display:block;text-align:right;color:var(--red)}
.community-box{left:581px;top:680px;width:235px;height:245px;background:#fff;border-radius:3px;box-shadow:0 0 3px #bbb}
.tile{position:absolute;width:92px}
.tile .photo{height:76px;border:2px solid #fff;box-shadow:0 0 1px #999}
.tile span{display:block;text-align:center;font-size:9.6px;color:#888;margin-top:8px}

/* footer */
.site-footer{left:0;top:958px;width:900px;height:218px;background:var(--footer)}
.fcol h4{font-family:"Oswald",sans-serif;font-weight:500;font-size:12.5px;color:#fff;padding-bottom:8px;border-bottom:1px solid #444;width:165px}
.circle{position:absolute;width:23px;height:23px;border-radius:50%;background:#4a4a4a}
.tweet{position:absolute;width:150px;font-family:Arial,sans-serif;font-size:9px;line-height:13.4px;color:#aaa;padding-left:16px}
.tweet::before{content:"";position:absolute;left:1px;top:3px;width:8px;height:8px;border-radius:50%;background:#ddd}
.tweet .dim{color:#666}
.tweet .ago{display:block;color:#fff;font-weight:bold;font-size:8px;margin-top:2px}
.fpost{position:absolute;width:170px;font-family:Arial,sans-serif;font-size:9px;line-height:13.4px;color:#666;padding-left:16px}
.fpost svg{position:absolute;left:0;top:1px}
.ftile{position:absolute;width:48px;height:48px;border:2px solid #ddd}
.footer-mark{left:100px;top:1122px;font-family:"Josefin Slab",serif;font-size:25px;color:#bdbdbd}
.copyright{left:0;top:1176px;width:900px;height:24px;background:var(--footer-base);text-align:center;line-height:24px;font-family:Arial,sans-serif;font-size:9.6px;color:#666}
</style>
</head>
<body>

<header class="abs site-header">
  <div class="abs brand"><span>Brookvale Funding</span><span class="brand-dot"></span></div>
  <div class="abs brand-sub">A Redfield Capital Company</div>
  <div class="abs contact">
    <div class="label">Work With Us</div>
    <div class="phone">555 0142 678</div>
    <div class="mail">mkettering@brookvalefunding.example</div>
  </div>
</header>

<nav class="abs main-nav">
  <a class="active" href="#">Home</a>
  <span class="sep" style="left:142px"></span>
  <a href="#" style="left:178px">About</a>
  <span class="sep" style="left:222px"></span>
  <a href="#" style="left:271px">Builders</a>
  <span class="sep" style="left:313px"></span>
  <a href="#" style="left:370px">Mortgage Info</a>
  <span class="sep" style="left:426px"></span>
  <a href="#" style="left:470px">Approval</a>
  <span class="sep" style="left:512px"></span>
  <a href="#" style="left:547px">Blog</a>
  <span class="sep" style="left:582px"></span>
  <a href="#" style="left:630px">Contact Us</a>
</nav>

<section class="abs hero">
  <div class="abs hero-frame"><div class="photo" role="img" aria-label="Team of mortgage professionals in business attire standing together"></div></div>
  <h1 class="abs">Earning Your Business</h1>
  <p class="abs"><b>Lorem Ipsum is simply dummy text of the printing and typesetting industry. Lorem Ipsum has been the industry's standard</b> dummy text ever since the 1500s, when an unknown printer took a galley of type and scrambled it to make a type specimen book. It has survived not only five centuries, but also the leap into electronic typesetting, remaining essentially unchanged. It was popularised in the 1960s with the release of Lettermark sheets containing Lorem Ipsum passages, and more recently with desktop publishing software......</p>
  <div class="abs btn">START HERE</div>
</section>
<div class="abs dash" style="left:0;top:417px;width:796px;border-color:#ddd"></div>

<section class="cred">
  <div class="abs" style="left:82px;top:447px">
    <h2 class="lead">Our Credentials</h2>
    <div class="tag">A Top Prodcer , Top-notch</div>
    <p style="margin-top:10px">You need a mortgage professional you can trust. You need a company that values honesty and integrity throughout the entire organization. You need to find strength, stability and opportunity -- especially now. You need me and Brookvale Funding!</p>
  </div>
  <div class="abs" style="left:358px;top:466px">
    <h2 class="plain">Awards</h2>
    <p style="margin-top:10px">You need a mortgage professional you can trust. You need a company that values honesty and integrity throughout the entire organization. You need to find strength, stability and opportunity -- especially now. You need me and Brookvale Funding!</p>
  </div>
  <div class="abs" style="left:603px;top:466px">
    <h2 class="plain">Recognition</h2>
    <p style="margin-top:10px">You need a mortgage professional you can trust. You need a company that values honesty and integrity throughout the entire organization. You need to find strength, stability and opportunity -- especially now. You need me and Brookvale Funding!</p>
  </div>
</section>
<div class="abs dash" style="left:86px;top:594px;width:730px"></div>

<h2 class="abs community-title" style="font-weight:400">Engaged in Our Community</h2>
<div class="abs community-sub">Connect With Us</div>
<svg class="abs" style="left:76px;top:662px" width="740" height="18" viewBox="0 0 740 18">
  <path d="M0 4 H350 L361 15 L372 4 H740" fill="none" stroke="#ddd" stroke-width="2"/>
</svg>

<h3 class="abs section-h" style="left:92px;top:688px;font-weight:400">Blog</h3>
<ul class="abs blog-list">
  <li><svg width="8" height="7"><path d="M0 0l4 3.5L0 7zM4 0l4 3.5L4 7z" fill="var(--red)"/></svg>Borrowing</li>
  <li><svg width="8" height="7"><path d="M0 0l4 3.5L0 7zM4 0l4 3.5L4 7z" fill="var(--red)"/></svg>Best Practices</li>
  <li><svg width="8" height="7"><path d="M0 0l4 3.5L0 7zM4 0l4 3.5L4 7z" fill="var(--red)"/></svg>Announcements</li>
  <li><svg width="8" height="7"><path d="M0 0l4 3.5L0 7zM4 0l4 3.5L4 7z" fill="var(--red)"/></svg>Resources</li>
  <li><svg width="8" height="7"><path d="M0 0l4 3.5L0 7zM4 0l4 3.5L4 7z" fill="var(--red)"/></svg>How To Guides</li>
  <li><svg width="8" height="7"><path d="M0 0l4 3.5L0 7zM4 0l4 3.5L4 7z" fill="var(--red)"/></svg>Builders Info</li>
</ul>

<h3 class="abs section-h" style="left:273px;top:688px;font-weight:400">Social</h3>
<div class="abs post" style="top:730px"><div class="thumb photo" role="img" aria-label="Portrait of a team member"></div><div class="txt"><b>You need a mortgage professional</b> you can trust. You need a company that values honesty and integrity....<span class="more">More</span></div></div>
<div class="abs post" style="top:791px"><div class="thumb photo" role="img" aria-label="Portrait of a team member"></div><div class="txt"><b>You need a mortgage professional</b> you can trust. You need a company that values honesty and integrity....<span class="more">More</span></div></div>
<div class="abs post" style="top:851px"><div class="thumb photo" role="img" aria-label="Portrait of a team member"></div><div class="txt"><b>You need a mortgage professional</b> you can trust. You need a company that values honesty and integrity....<span class="more">More</span></div></div>

<aside class="abs community-box">
  <h3 class="abs section-h" style="left:15px;top:6px;font-weight:400">In The Community</h3>
  <div class="tile" style="left:15px;top:40px"><div class="photo warm" role="img" aria-label="Team meeting around a conference table"></div><span>You need a mortgage</span></div>
  <div class="tile" style="left:126px;top:40px"><div class="photo" role="img" aria-label="Colleagues reviewing documents together"></div><span>You need a mortgage</span></div>
  <div class="tile" style="left:15px;top:144px"><div class="photo" role="img" aria-label="Group working at a table with laptops"></div><span>You need a mortgage</span></div>
  <div class="tile" style="left:126px;top:144px"><div class="photo" role="img" aria-label="Team member standing in an office"></div><span>You need a mortgage</span></div>
</aside>
<div class="abs dash" style="left:76px;top:944px;width:730px"></div>

<footer class="abs site-footer"></footer>
<div class="abs fcol" style="left:94px;top:986px"><h4>SOCIAL NETWORKS</h4></div>
<span class="circle" style="left:95px;top:1023px"></span>
<span class="circle" style="left:123px;top:1023px"></span>
<span class="circle" style="left:150px;top:1023px"></span>
<span class="circle" style="left:178px;top:1023px"></span>
<span class="circle" style="left:206px;top:1023px"></span>
<div class="abs fcol" style="left:94px;top:1074px"><h4>NEED AN ANSWER?</h4></div>
<div class="abs footer-mark">marisolkettering</div>

<div class="abs fcol" style="left:274px;top:986px"><h4>LATEST UPDATES</h4></div>
<div class="tweet" style="left:274px;top:1022px">Check out this great <span class="dim">#themeshelf</span> item 'Aurora - Responsive Blog Theme' <span class="dim">http://sh.rt/KQ7mWx2</span><span class="ago">71 days ago</span></div>
<div class="tweet" style="left:274px;top:1103px">Check out this great <span class="dim">#themeshelf</span> item 'Swift - Responsive HTML Template' <span class="dim">http://sh.rt/Bp4nRt8</span><span class="ago">91 days ago</span></div>

<div class="abs fcol" style="left:454px;top:986px"><h4>FROM THE BLOG</h4></div>
<div class="fpost" style="left:454px;top:1022px"><svg width="10" height="10"><rect x="0.5" y="1.5" width="9" height="8" fill="none" stroke="#aaa"/><path d="M0.5 3.5h9" stroke="#aaa"/></svg>This is a Standard Post format (with image)</div>
<div class="fpost" style="left:454px;top:1063px"><svg width="10" height="10"><rect x="0.5" y="1.5" width="9" height="8" fill="none" stroke="#aaa"/><path d="M0.5 3.5h9" stroke="#aaa"/></svg>This is a Gallery Post Format</div>
<div class="fpost" style="left:454px;top:1090px;white-space:nowrap"><svg width="10" height="10"><rect x="0.5" y="1.5" width="9" height="8" fill="none" stroke="#aaa"/><path d="M0.5 3.5h9" stroke="#aaa"/></svg>This is a Video Post Format (Vidzo)</div>
<div class="fpost" style="left:454px;top:1117px;width:150px"><svg width="10" height="10"><rect x="0.5" y="1.5" width="9" height="8" fill="none" stroke="#aaa"/><path d="M0.5 3.5h9" stroke="#aaa"/></svg>This is a Video Post Format (ClipTube)</div>

<div class="abs fcol" style="left:634px;top:986px"><h4>PHOTO STREAM</h4></div>
<div class="ftile photo" style="left:634px;top:1022px" role="img" aria-label="Community photo"></div>
<div class="ftile photo warm" style="left:692px;top:1022px" role="img" aria-label="Community photo"></div>
<div class="ftile photo" style="left:750px;top:1022px" role="img" aria-label="Community photo"></div>
<div class="ftile photo warm" style="left:634px;top:1080px" role="img" aria-label="Community photo"></div>
<div class="ftile photo" style="left:692px;top:1080px" role="img" aria-label="Community photo"></div>
<div class="ftile photo warm" style="left:750px;top:1080px" role="img" aria-label="Community photo"></div>

<div class="abs copyright">2013 © marisolkettering. ALL Rights Reserved. Privacy Policy | Terms of Service</div>

</body>
</html>
```